'Little Lantern' promotional brochure

We have designed a 6 week program to educate impending first-time parents about the things they need to know to survive the first 6 months. Sessions delivered by general practitioner/family doctor, dietician, physiotherapist, speech pathologist and psychologist. Our promotional blurb is: 'A comprehensive education program for first-time parents-to-be, delivered over 6 weeks by health professionals in your community, about everything you need to know to look after your baby (and yourself!) in the first 6 months'. I now want to put together a promotional brochure to be distributed to those couples who express an interest which will provide further details of what will be delivered in the course.
Updates
In terms of layout, I envisaged a double sided A4 size, foldable into 3 sections, but very happy to be guided on this.
Target Market(s)
To appeal to a young, well educated demographic. First time parents couples.
Industry/Entity Type
Medical
Font styles to use
Other font styles liked:
- Playfair Display
Requirements
Must have
- Playfair display font to be consistent with our logo (attached). Logo also included please. Some consistency with colours of logo please.
Nice to have
- I am a doctor, and have no creative genes! But prefer a clean and professional appearance overall. Not too cluttered in overall appearance.
Should not have
- No cheesy pictures of babies.

```html
<!DOCTYPE html>
<html lang="en">
<head>
<meta charset="utf-8">
<title>Little Lantern – Program Brochure, Inside Spread</title>
<link href="https://fonts.googleapis.com/css2?family=Raleway:wght@400;500;700;900&display=swap" rel="stylesheet">
<style>
  :root {
    --page-bg: #ededed;
    --paper: #ffffff;
    --panel-tint: #f3f3f3;
    --photo-dark: #3a3a3a;
    --photo-mid: #8a8a8a;
    --photo-light: #d9d9d9;
    --accent-green: #7cc520;
    --rule-grey: #5a5a5a;
    --text-dark: #262626;
    --text-body: #3d3d3d;
    --fold-line: rgba(0,0,0,0.08);
  }
  * { box-sizing: border-box; margin: 0; padding: 0; }
  html, body {
    width: 1200px; height: 801px; overflow: hidden;
    background: var(--page-bg);
    font-family: "Raleway", sans-serif;
    color: var(--text-body);
  }
  .brochure {
    position: absolute; left: 50px; top: 12px;
    width: 1100px; height: 777px;
    background: var(--paper);
    box-shadow: 0 6px 24px rgba(0,0,0,0.12);
    overflow: hidden;
  }
  .hero-photo {
    position: absolute; left: 0; top: 0; width: 100%; height: 268px;
    background: linear-gradient(100deg, var(--photo-light) 0%, var(--photo-mid) 35%, var(--photo-light) 55%, var(--photo-mid) 75%, var(--photo-dark) 100%);
  }
  .backdrop-photo {
    position: absolute; left: 367px; top: 268px; width: 733px; height: 509px;
    background: radial-gradient(ellipse at 55% 55%, #d6d6d6 0%, #e8e8e8 45%, var(--panel-tint) 75%);
  }
  .panel {
    position: absolute; top: 268px; width: 366.67px; height: 509px;
    padding: 22px 28px 20px 30px;
    display: flex; flex-direction: column; gap: 16px;
  }
  .panel--left { left: 0; background: var(--panel-tint); }
  .panel--middle { left: 366.67px; }
  .panel--right { left: 733.33px; }
  .fold { position: absolute; top: 0; width: 1px; height: 100%; background: var(--fold-line); }
  .fold--one { left: 366.67px; }
  .fold--two { left: 733.33px; }

  .week { display: flex; flex-direction: column; gap: 6px; }
  .week-heading {
    position: relative; height: 22px; margin-left: -30px;
    display: flex; align-items: center;
  }
  .week-heading::before {
    content: ""; position: absolute; left: 0; top: 5px;
    width: 120px; height: 14px; background: var(--accent-green);
  }
  .week-heading::after {
    content: ""; position: absolute; left: 120px; right: -28px; top: 11px;
    height: 3px; background: var(--rule-grey);
  }
  .week-title {
    position: relative; z-index: 1; padding-left: 34px;
    font-weight: 900; font-size: 19px; color: var(--text-dark);
  }
  .week-text { font-size: 11.8px; line-height: 1.45; }
  .week-text strong { font-weight: 700; color: var(--text-dark); }
  .session + .session { margin-top: 4px; }

  .topic-list { list-style: none; display: flex; flex-direction: column; gap: 3px; margin-top: 2px; }
  .topic-list li { display: flex; align-items: center; gap: 7px; font-size: 11.8px; line-height: 1.35; }
  .tick { width: 12px; height: 12px; flex: none; }
</style>
</head>
<body>
<main class="brochure" aria-label="Little Lantern program brochure, inside spread">
  <div class="hero-photo" role="img" aria-label="Black and white photo of a parent holding a newborn baby against their chest"></div>
  <div class="backdrop-photo" role="img" aria-label="Faint black and white photo of a stethoscope resting on medical notes"></div>

  <section class="panel panel--left">
    <article class="week">
      <h2 class="week-heading"><span class="week-title">Week 1</span></h2>
      <p class="week-text">GP Dr Helena Marsh will share information for Mum's own health after delivery. Topics include:</p>
      <ul class="topic-list">
        <li><svg class="tick" viewBox="0 0 12 12"><circle cx="6" cy="6" r="5.2" fill="none" stroke="#7cc520" stroke-width="1.2"/><path d="M3.3 6.2l1.9 1.9 3.6-4" fill="none" stroke="#7cc520" stroke-width="1.5"/></svg>Vaccinations in pregnancy</li>
        <li><svg class="tick" viewBox="0 0 12 12"><circle cx="6" cy="6" r="5.2" fill="none" stroke="#7cc520" stroke-width="1.2"/><path d="M3.3 6.2l1.9 1.9 3.6-4" fill="none" stroke="#7cc520" stroke-width="1.5"/></svg>Bleeding, bladder and bowel after delivery</li>
        <li><svg class="tick" viewBox="0 0 12 12"><circle cx="6" cy="6" r="5.2" fill="none" stroke="#7cc520" stroke-width="1.2"/><path d="M3.3 6.2l1.9 1.9 3.6-4" fill="none" stroke="#7cc520" stroke-width="1.5"/></svg>Breastfeeding, engorgement and mastitis</li>
        <li><svg class="tick" viewBox="0 0 12 12"><circle cx="6" cy="6" r="5.2" fill="none" stroke="#7cc520" stroke-width="1.2"/><path d="M3.3 6.2l1.9 1.9 3.6-4" fill="none" stroke="#7cc520" stroke-width="1.5"/></svg>Bottle feeding</li>
        <li><svg class="tick" viewBox="0 0 12 12"><circle cx="6" cy="6" r="5.2" fill="none" stroke="#7cc520" stroke-width="1.2"/><path d="M3.3 6.2l1.9 1.9 3.6-4" fill="none" stroke="#7cc520" stroke-width="1.5"/></svg>Post-natal anxiety &amp; depression</li>
        <li><svg class="tick" viewBox="0 0 12 12"><circle cx="6" cy="6" r="5.2" fill="none" stroke="#7cc520" stroke-width="1.2"/><path d="M3.3 6.2l1.9 1.9 3.6-4" fill="none" stroke="#7cc520" stroke-width="1.5"/></svg>Intimacy and contraception</li>
      </ul>
    </article>
    <article class="week">
      <h2 class="week-heading"><span class="week-title">Week 2</span></h2>
      <p class="week-text session"><strong>Session 1</strong> – Clinical Psychologist Dr Anya Whitford will discuss changes in relationships as couples become parents, gender roles in parenting and post-natal depression.</p>
      <p class="week-text session"><strong>Session 2</strong> – Physiotherapist Rosa Linwood will present advice for Mums regarding exercise during and after pregnancy, looking after the pelvic floor during and after pregnancy, and abdominal muscle separation management. She will also provide advice for promoting babies' neck strength and minimising the risk of flat spots on the head and encouraging gross motor skills in the first 6 months.</p>
    </article>
  </section>

  <section class="panel panel--middle">
    <article class="week">
      <h2 class="week-heading"><span class="week-title">Week 3</span></h2>
      <p class="week-text"><strong>Session 1</strong> – Dietician Clare Denholm provides advice for Mums regarding healthy eating during pregnancy and lactation, normal weight gain during pregnancy and realistic weight loss after. She will also discuss the evidence regarding breastfeeding VS bottle-feeding, normal infant weight gain and introducing solids (including those with potential for allergy).</p>
    </article>
    <article class="week">
      <h2 class="week-heading"><span class="week-title">Week 4</span></h2>
      <p class="week-text">GP Dr Helena Marsh will share advice about your babies' health in the first 6 months, including:</p>
      <ul class="topic-list">
        <li><svg class="tick" viewBox="0 0 12 12"><circle cx="6" cy="6" r="5.2" fill="none" stroke="#7cc520" stroke-width="1.2"/><path d="M3.3 6.2l1.9 1.9 3.6-4" fill="none" stroke="#7cc520" stroke-width="1.5"/></svg>Skin of newborns</li>
        <li><svg class="tick" viewBox="0 0 12 12"><circle cx="6" cy="6" r="5.2" fill="none" stroke="#7cc520" stroke-width="1.2"/><path d="M3.3 6.2l1.9 1.9 3.6-4" fill="none" stroke="#7cc520" stroke-width="1.5"/></svg>Sleeping</li>
        <li><svg class="tick" viewBox="0 0 12 12"><circle cx="6" cy="6" r="5.2" fill="none" stroke="#7cc520" stroke-width="1.2"/><path d="M3.3 6.2l1.9 1.9 3.6-4" fill="none" stroke="#7cc520" stroke-width="1.5"/></svg>Crying</li>
        <li><svg class="tick" viewBox="0 0 12 12"><circle cx="6" cy="6" r="5.2" fill="none" stroke="#7cc520" stroke-width="1.2"/><path d="M3.3 6.2l1.9 1.9 3.6-4" fill="none" stroke="#7cc520" stroke-width="1.5"/></svg>Immunisations</li>
        <li><svg class="tick" viewBox="0 0 12 12"><circle cx="6" cy="6" r="5.2" fill="none" stroke="#7cc520" stroke-width="1.2"/><path d="M3.3 6.2l1.9 1.9 3.6-4" fill="none" stroke="#7cc520" stroke-width="1.5"/></svg>Fever and infections</li>
        <li><svg class="tick" viewBox="0 0 12 12"><circle cx="6" cy="6" r="5.2" fill="none" stroke="#7cc520" stroke-width="1.2"/><path d="M3.3 6.2l1.9 1.9 3.6-4" fill="none" stroke="#7cc520" stroke-width="1.5"/></svg>Diarrhoea and constipation</li>
        <li><svg class="tick" viewBox="0 0 12 12"><circle cx="6" cy="6" r="5.2" fill="none" stroke="#7cc520" stroke-width="1.2"/><path d="M3.3 6.2l1.9 1.9 3.6-4" fill="none" stroke="#7cc520" stroke-width="1.5"/></svg>Teething</li>
        <li><svg class="tick" viewBox="0 0 12 12"><circle cx="6" cy="6" r="5.2" fill="none" stroke="#7cc520" stroke-width="1.2"/><path d="M3.3 6.2l1.9 1.9 3.6-4" fill="none" stroke="#7cc520" stroke-width="1.5"/></svg>Understanding a baby's signals</li>
      </ul>
    </article>
  </section>

  <section class="panel panel--right">
    <article class="week">
      <h2 class="week-heading"><span class="week-title">Week 5</span></h2>
      <p class="week-text"><strong>Session 1</strong> – Clinical Psychologist Dr Anya Whitford will share information about bonding &amp; attachment with your baby, how to promote their social &amp; emotional development and how to manage separation anxiety. She will also discuss positive parenting approaches.</p>
    </article>
    <article class="week">
      <h2 class="week-heading"><span class="week-title">Week 6</span></h2>
      <p class="week-text session"><strong>Session 1</strong> – Dads' Round Table – a men-only session (including beer!) with a new father for frank discussion about the road ahead. Mums will do a shopping excursion with the GP &amp; Dietician to Greenway Market to look at baby products and food – the good and the bad!</p>
      <p class="week-text session"><strong>Session 2</strong> – Program review: reflection and evaluation and future session planning when baby is 6 months of age.</p>
    </article>
  </section>

  <div class="fold fold--one"></div>
  <div class="fold fold--two"></div>
</main>
</body>
</html>
```